Display Carton for cinnamon sticks

Display Box Specification – Valle del Sol Dorado Cinnamon Sticks
Design a retail-ready display box for Valle del Sol Dorado cinnamon sticks, sourced from Sri Lanka. Each selling unit contains two 5" cinnamon sticks, individually sealed in a clear cellophane wrapper to preserve freshness and showcase product quality.
📦 Carton Configuration
• Total Units per Display: 32 wrappers
• Layering Structure: 8 wrappers per layer × 4 layers high
• Orientation: Wrappers laid flat, stacked horizontally for optimal visibility and ease of access
I uploaded 2 AI-generated images for reference purposes only

Target Market(s)

Cultural Appeal Suggestions Color Palette: Use warm, earthy tones like terracotta, deep reds, and golds—colors often associated with Latin American aesthetics. Typography: Consider a bold, rustic font with a handcrafted feel to evoke authenticity. Language: Include bilingual labeling (English & Spanish). For example: “Cinnamon Sticks” → “Palitos de Canela” “Sourced from Sri Lanka” → “Origen: Sri Lanka” Storytelling Element: Add a short cultural or culinary note about how cinnamon is used in Latin cuisine (e.g., in café de olla, arroz con leche, or ponche).

Font styles to use
Other font styles liked:
• Consider a bold, rustic font with a handcrafted feel to evoke authenticity.

Requirements
Nice to have
• 📦 Display Box Messaging Front panel: “Valle del Sol Dorado – Premium Canela de Ceilán” (Ceylon Cinnamon – Naturally Sweet & Aromatic) Side panel: “Perfect for traditional recipes and everyday flavor” (Ideal para recetas tradicionales y sabor diario)

```html
<!DOCTYPE html>
<html lang="en">
<head>
<meta charset="utf-8">
<title>Valle del Sol Dorado – Cinnamon Sticks Carton</title>
<link rel="stylesheet" href="https://fonts.googleapis.com/css2?family=Cinzel:wght@500;700&family=Roboto:wght@400&display=swap">
<style>
  :root {
    --backdrop: #d9d9d9;
    --carton-brown: #5b3a33;
    --label-gold: #f3b64c;
    --side-gold: #eea83c;
    --ink: #3a2318;
    --band-green: #1f7a3c;
    --band-red: #e4573a;
    --band-blue: #2a4c9a;
    --band-yellow: #f6b83c;
  }
  * { box-sizing: border-box; margin: 0; padding: 0; }
  html, body { width: 1200px; height: 800px; overflow: hidden; background: var(--backdrop); }
  body { position: relative; font-family: "Roboto", sans-serif; color: var(--ink); }

  .pattern-band {
    position: absolute; inset: 0;
    background: linear-gradient(90deg, var(--band-green), var(--band-red) 35%, var(--band-yellow) 50%, var(--band-red) 65%, var(--band-green));
  }
  .emblem-spot { flex: none; width: 56px; height: 40px; border-radius: 4px;
    background: linear-gradient(135deg, #d39b45, #b77d33); }

  /* Top (lid) panel */
  .lid { position: absolute; left: 240px; top: 30px; width: 930px; height: 300px; }
  .lid-label { position: absolute; inset: 24px; background: var(--label-gold); border: 1.5px solid var(--ink); }
  .lid-origin { position: absolute; left: 20px; top: 18px; display: flex; align-items: center; gap: 10px;
    font-family: "Cinzel", serif; }
  .lid-origin .small { font-size: 11px; letter-spacing: 3px; line-height: 1.3; }
  .lid-origin .big { font-size: 20px; font-weight: 700; letter-spacing: 2px; line-height: 1.2; }
  .lid-photo { position: absolute; left: 20px; top: 130px; width: 150px; height: 96px; border-radius: 6px;
    background: linear-gradient(135deg, #c98a55, #8a4f2a); }
  .lid-copy { position: absolute; left: 220px; top: 20px; width: 390px; font-size: 13px; line-height: 1.5; }
  .lid-rule { position: absolute; left: 220px; width: 390px; top: 112px; border-top: 1.5px solid var(--ink); }
  .lid-tagline { position: absolute; left: 220px; top: 126px; width: 400px; font-family: "Cinzel", serif;
    font-weight: 700; font-size: 13px; line-height: 1.35; letter-spacing: 0.5px; }
  .lid-brand { position: absolute; right: 20px; top: 18px; width: 230px; text-align: right; font-family: "Cinzel", serif; }
  .lid-brand .brand-name { font-weight: 700; font-size: 24px; line-height: 1.1; }
  .lid-brand .product { font-size: 17px; letter-spacing: 2px; margin-top: 16px; }
  .lid-brand .count { font-weight: 700; font-size: 56px; line-height: 1; margin-top: 16px; }
  .lid-brand .count span { font-size: 17px; font-weight: 500; letter-spacing: 2px; }

  /* End side panel */
  .side { position: absolute; left: 30px; top: 350px; width: 190px; height: 420px; }
  .side-label { position: absolute; inset: 14px; background: var(--side-gold); border: 1.2px solid var(--ink);
    padding: 12px; display: flex; flex-direction: column; gap: 8px; }
  .side .brand-name { font-family: "Cinzel", serif; font-weight: 700; font-size: 14px; line-height: 1.15; }
  .side .product { font-family: "Cinzel", serif; font-size: 11px; letter-spacing: 1px; }
  .side .count { font-family: "Cinzel", serif; font-weight: 700; font-size: 34px; line-height: 1; }
  .side .count span { font-size: 11px; font-weight: 500; letter-spacing: 1px; }
  .side .tagline { font-family: "Cinzel", serif; font-weight: 700; font-size: 9px; line-height: 1.3;
    border-top: 1px solid var(--ink); padding-top: 6px; }
  .side .copy { font-size: 9px; line-height: 1.4; }
  .side .photo { height: 44px; border-radius: 4px; background: linear-gradient(135deg, #c98a55, #8a4f2a); }
  .side .origin { display: flex; align-items: center; gap: 8px; font-family: "Cinzel", serif; }
  .side .origin .emblem-spot { width: 40px; height: 30px; }
  .side .origin .small { font-size: 8px; letter-spacing: 1px; line-height: 1.3; }
  .side .origin .big { font-size: 13px; font-weight: 700; }

  /* Front panel */
  .front { position: absolute; left: 240px; top: 350px; width: 930px; height: 420px; background: var(--carton-brown); }
  .front .pattern-band { inset: 18px; border-radius: 24px; }
  .front-label { position: absolute; inset: 50px; background: var(--label-gold); border-radius: 14px; }
  .brand-lockup { position: absolute; left: 0; right: 0; top: 16px; text-align: center; font-family: "Cinzel", serif;
    font-weight: 700; font-size: 32px; letter-spacing: 1px; }
  .title-box { position: absolute; left: 40px; right: 40px; top: 72px; height: 150px; border: 1.5px solid var(--ink); }
  .product-title { position: absolute; left: 0; right: 0; top: 18px; text-align: center;
    font-family: "Cinzel", serif; font-weight: 700; font-size: 50px; letter-spacing: 3px; line-height: 1.2; }
  .title-rule { position: absolute; left: 30px; right: 30px; top: 90px; border-top: 1.5px solid var(--ink); }
  .origin-line { position: absolute; left: 0; right: 0; top: 98px; display: flex; justify-content: center;
    align-items: center; gap: 12px; font-family: "Cinzel", serif; }
  .origin-line .small { font-size: 11px; letter-spacing: 2px; }
  .origin-line .big { font-size: 19px; font-weight: 700; letter-spacing: 2px; }
  .ornament-strip { position: absolute; left: 20px; right: 20px; bottom: 14px; height: 60px; border-radius: 6px;
    background: linear-gradient(90deg, #d9973c, #c07b2d 50%, #d9973c); }
</style>
</head>
<body>

<section class="lid" aria-label="Top panel">
  <div class="pattern-band" role="img" aria-label="Zigzag border pattern in green, red and blue"></div>
  <div class="lid-label">
    <div class="lid-origin">
      <div class="emblem-spot" role="img" aria-label="Origin emblem illustration"></div>
      <div><div class="small">PREMIUM<br>CANELA DE</div><div class="big">CEILÁN</div></div>
    </div>
    <div class="lid-photo" role="img" aria-label="Photo of bundled cinnamon sticks"></div>
    <p class="lid-copy">Lorem ipsum dolor sit amet, consectetur adipiscing elit. Nulla ac sapien non tellus blandit fringilla. Pellentesque at elit molestie, gravida dui non, venenatis erat. Proin eget risus eu purus mollis porta.</p>
    <div class="lid-rule"></div>
    <p class="lid-tagline">PERFECT FOR TRADITIONAL RECIPES<br>AND EVERYDAY FLAVOR<br>(IDEAL PARA RECETAS TRADICIONALES Y<br>SABOR DIARIO)</p>
    <div class="lid-brand">
      <div class="brand-name">Valle del Sol Dorado</div>
      <div class="product">CINAMON STICKS</div>
      <div class="count">25 <span>STICKS</span></div>
    </div>
  </div>
</section>

<section class="side" aria-label="End panel">
  <div class="pattern-band" role="img" aria-label="Zigzag border pattern in green, red and blue"></div>
  <div class="side-label">
    <div class="brand-name">Valle del Sol Dorado</div>
    <div class="product">CINAMON STICKS</div>
    <div class="count">25 <span>STICKS</span></div>
    <p class="tagline">PERFECT FOR TRADITIONAL RECIPES AND EVERYDAY FLAVOR (IDEAL PARA RECETAS TRADICIONALES Y SABOR DIARIO)</p>
    <p class="copy">Lorem ipsum dolor sit amet, consectetur adipiscing elit. Nulla ac sapien non tellus blandit fringilla.</p>
    <div class="photo" role="img" aria-label="Photo of bundled cinnamon sticks"></div>
    <div class="origin">
      <div class="emblem-spot" role="img" aria-label="Origin emblem illustration"></div>
      <div><div class="small">PREMIUM<br>CANELA DE</div><div class="big">CEILÁN</div></div>
    </div>
  </div>
</section>

<section class="front" aria-label="Front panel">
  <div class="pattern-band" role="img" aria-label="Zigzag border pattern in green, red and blue"></div>
  <div class="front-label">
    <div class="brand-lockup">Valle del Sol Dorado</div>
    <div class="title-box">
      <h1 class="product-title">CINAMON STICKS</h1>
      <div class="title-rule"></div>
      <div class="origin-line">
        <div class="emblem-spot" role="img" aria-label="Origin emblem illustration"></div>
        <div><div class="small">PREMIUM CANELA DE</div><div class="big">CEILÁN</div></div>
      </div>
    </div>
    <div class="ornament-strip" role="img" aria-label="Carved floral ornament band"></div>
  </div>
</section>

</body>
</html>
```